We’re a real estate firm that has landed a big builder in a neighboring state. Our branding needs...

We are a real estate firm who represents various builders along with doing resale here in Oregon. Our firm is growing to represent a big builder in Washington State and we’ll have another 40 brokers on our team. We need rebranding. As in, a new logo ( the house logo we have now looks cartoonish, hate it). We need new cards, something to really stand out. I’ve been thinking of using those NFC cards from ZEP or the ones with the seam color. I likely want two or three designs, a darker (as in a background color of black or grey) , a light one ( again I mean background color) and a credit card style (either plastic w an embossed name/number on front, or metal ). I’m thinking dark background for cc, or silver if it’s metal. That’s my thoughts, but you are the artists, so maybe you have an idea I haven’t considered. Our colors were black and red, but we don’t have to stick to that. Just nothing too busy. Oh, and we are typically representing the local, higher quality builders in our area (just below custom), but not national. Subdivisions are near the Kell Varney, Brisco, and Thornfield Crest sites. We are super excited, but without a lot of time to change the “look” of our brokerage. So I’ll be deciding and moving forward within 24 hours tops. Our name is Real Estate Summit Alliance ( we cant change the name because of timeline and business license) Thank you!

Industry/Entity Type

Real Estate

Contact Information for Business Card

The usual. Name of firm. Name of cardholder. Contact info.

Font styles to use
Serif
Sans Serif

Colors

Designer to choose colors to be used in the design.

Requirements
Must have
• A sleek or simple look. I included photos of cards with stylistic attributes we like. Thank you
Nice to have
• We really like the black backgrounds. With foil or embossed detail. We also like the black on black. Matte black card with raised shiny black detail. But still eye catching.
Should not have
• No ornate or busy looking style. We don’t want anything cluttered.

```html
<!DOCTYPE html>
<html lang="en">
<head>
<meta charset="utf-8">
<title>Real Estate Summit Alliance – Business Card</title>
<link href="https://fonts.googleapis.com/css2?family=Lato:wght@400;700&display=swap" rel="stylesheet">
<style>
  :root {
    --stage: #414141;
    --navy: #0f2f5f;
    --ink: #1a1a1a;
    --paper: #ffffff;
    --rule: #d4d4d4;
    --shadow: rgba(0,0,0,0.55);
  }
  * { margin: 0; padding: 0; box-sizing: border-box; }
  html, body { width: 1200px; height: 900px; overflow: hidden; }
  body {
    background: var(--stage);
    font-family: "Lato", sans-serif;
    position: relative;
  }
  .card {
    position: absolute;
    width: 477px;
    height: 293px;
    box-shadow: 3px 5px 8px var(--shadow);
  }
  .card-front {
    left: 120px; top: 275px;
    background: var(--paper);
    border-radius: 0 46px 0 46px;
  }
  .card-back {
    left: 607px; top: 275px;
    height: 291px;
    background: var(--navy);
    border-radius: 46px 0 46px 0;
    display: flex; flex-direction: column; align-items: center; justify-content: center;
  }
  .front-brand {
    position: absolute;
    left: 30px; top: 80px;
    width: 200px; height: 132px;
    display: flex; flex-direction: column; align-items: center; justify-content: center;
    gap: 10px;
    color: var(--navy);
    font-weight: 700;
    text-align: center;
    line-height: 1.15;
    font-size: 21px;
  }
  .brand-square { width: 16px; height: 16px; background: var(--navy); }
  .divider {
    position: absolute;
    left: 238px; top: 73px;
    width: 1px; height: 147px;
    background: var(--rule);
  }
  .details {
    position: absolute;
    left: 263px; top: 70px;
    color: var(--ink);
    font-size: 14px;
    line-height: 17.5px;
  }
  .holder-name {
    color: var(--navy);
    font-weight: 700;
    font-size: 18px;
    letter-spacing: 0.4px;
    line-height: 22px;
  }
  .holder-role { margin-bottom: 4px; }
  .contact-line { display: flex; align-items: center; gap: 4px; }
  .contact-line svg { width: 10px; height: 10px; fill: var(--navy); flex: none; }
  .address { margin-top: 6px; }
  .back-wordmark {
    color: var(--paper);
    font-weight: 700;
    text-align: center;
    margin-top: 20px;
  }
  .back-wordmark .primary { display: block; font-size: 40px; line-height: 44px; }
  .back-wordmark .secondary { display: block; font-size: 15px; letter-spacing: 2.2px; line-height: 20px; }
  .back-square { width: 18px; height: 18px; background: var(--paper); }
</style>
</head>
<body>
  <section class="card card-front">
    <div class="front-brand">
      <span class="brand-square"></span>
      <span>Real Estate<br>Summit Alliance</span>
    </div>
    <div class="divider"></div>
    <div class="details">
      <p class="holder-name">MARCUS ELLERY</p>
      <p class="holder-role">Managing Director</p>
      <p class="contact-line"><svg viewBox="0 0 10 10"><path d="M2 1l2 2-1 1c.6 1.3 1.7 2.4 3 3l1-1 2 2-1.5 1.5C4 9 1 6 .5 2.5z"/></svg>503-418 207 556</p>
      <p class="contact-line"><svg viewBox="0 0 10 10"><path d="M3 0h4a1 1 0 0 1 1 1v8a1 1 0 0 1-1 1H3a1 1 0 0 1-1-1V1a1 1 0 0 1 1-1zm0 1.5v6h4v-6z"/></svg>503-418 207 556</p>
      <p class="contact-line"><svg viewBox="0 0 10 10"><path d="M0 2h10v6H0zm1 1l4 3 4-3z" fill-rule="evenodd"/></svg>hello@summitalliance.co</p>
      <p class="contact-line"><svg viewBox="0 0 10 10"><circle cx="5" cy="5" r="5"/></svg>www.summitalliance.co</p>
      <p class="address">12345, Address Goes Here<br>Country Name, 123456.</p>
    </div>
  </section>

  <section class="card card-back">
    <span class="back-square"></span>
    <p class="back-wordmark">
      <span class="primary">Real Estate</span>
      <span class="secondary">SUMMIT ALLIANCE</span>
    </p>
  </section>
</body>
</html>
```